Business card for a new cabinet shop company named Veloran Cabinets for high end cabinets

Design a business card, thinking dark rich green with colours to speak of high end luxury ie; cream, gold, black possibly

Mitchell Tarrowby
Director Craftsman
Email: info@veloranjoinery-example.com.au
Instagram : @veloran.cabinets

```html
<!DOCTYPE html>
<html lang="en">
<head>
<meta charset="UTF-8">
<title>Veloran Cabinets — Business Card</title>
<link rel="stylesheet" href="https://fonts.googleapis.com/css2?family=Poppins:wght@400;500;600&display=swap">
<style>
  :root {
    --backdrop: #131615;
    --card: #1b2e25;
    --card-edge: #25392f;
    --gold: #c8a35a;
    --ivory: #f3f0ea;
    --font-text: "Poppins", sans-serif;
  }
  * { box-sizing: border-box; margin: 0; padding: 0; }
  html, body {
    width: 1200px;
    height: 800px;
    overflow: hidden;
    background: var(--backdrop);
    font-family: var(--font-text);
  }
  .canvas {
    width: 1200px;
    height: 800px;
    display: flex;
    align-items: center;
    justify-content: center;
    gap: 40px;
  }
  .card {
    width: 540px;
    height: 309px;
    background: var(--card);
    border: 1px solid var(--card-edge);
    border-radius: 18px;
    position: relative;
    overflow: hidden;
  }

  /* Front */
  .card--front {
    display: flex;
    align-items: center;
    justify-content: center;
  }
  .brand {
    display: flex;
    align-items: center;
    gap: 16px;
  }
  .brand__square {
    width: 34px;
    height: 34px;
    border: 2px solid var(--gold);
  }
  .brand__name {
    color: var(--gold);
    font-weight: 500;
    font-size: 34px;
    letter-spacing: 0.02em;
  }

  /* Back */
  .card--back {
    display: flex;
    align-items: center;
    padding: 0 36px 0 44px;
  }
  .back-mark {
    width: 168px;
    flex: none;
    color: var(--gold);
    font-weight: 500;
    font-size: 24px;
    line-height: 1.2;
    letter-spacing: 0.02em;
  }
  .contact-block {
    flex: 1;
    min-width: 0;
    padding-left: 18px;
  }
  .company-title {
    color: var(--ivory);
    font-weight: 500;
    font-size: 19px;
    letter-spacing: 0.04em;
    margin-bottom: 14px;
  }
  .person {
    display: flex;
    gap: 12px;
    margin-bottom: 16px;
  }
  .person__rule {
    width: 2px;
    background: var(--gold);
  }
  .person__name {
    color: var(--ivory);
    font-weight: 600;
    font-size: 17px;
    line-height: 1.25;
  }
  .person__role {
    color: var(--gold);
    font-size: 11px;
    letter-spacing: 0.02em;
  }
  .contact-list {
    list-style: none;
    display: grid;
    gap: 6px;
  }
  .contact-list__item {
    display: flex;
    align-items: center;
    gap: 9px;
    color: var(--ivory);
    font-size: 10.5px;
    white-space: nowrap;
  }
  .contact-list__icon {
    width: 11px;
    height: 11px;
    flex: none;
    color: var(--gold);
  }
</style>
</head>
<body>
  <main class="canvas">
    <section class="card card--front" aria-label="Card front">
      <div class="brand">
        <span class="brand__square"></span>
        <span class="brand__name">Veloran Cabinets</span>
      </div>
    </section>

    <section class="card card--back" aria-label="Card back">
      <div class="back-mark">Veloran<br>Cabinets</div>
      <div class="contact-block">
        <h1 class="company-title">VELORAN CABINETS</h1>
        <div class="person">
          <span class="person__rule"></span>
          <div>
            <p class="person__name">Mitchell Tarrowby</p>
            <p class="person__role">Director Craftsman</p>
          </div>
        </div>
        <ul class="contact-list">
          <li class="contact-list__item">
            <svg class="contact-list__icon" viewBox="0 0 24 24" aria-hidden="true"><path fill="currentColor" d="M6.6 10.8a15.1 15.1 0 0 0 6.6 6.6l2.2-2.2a1 1 0 0 1 1-.25 11.4 11.4 0 0 0 3.6.57 1 1 0 0 1 1 1V20a1 1 0 0 1-1 1A17 17 0 0 1 3 4a1 1 0 0 1 1-1h3.5a1 1 0 0 1 1 1c0 1.25.2 2.45.57 3.57a1 1 0 0 1-.25 1z"/></svg>
            (123) 555-0148
          </li>
          <li class="contact-list__item">
            <svg class="contact-list__icon" viewBox="0 0 24 24" aria-hidden="true"><path fill="currentColor" d="M2 5h20v14H2zm2 2v.4l8 5.1 8-5.1V7z"/></svg>
            info@veloranjoinery-example.com.au
          </li>
          <li class="contact-list__item">
            <svg class="contact-list__icon" viewBox="0 0 24 24" aria-hidden="true"><circle cx="12" cy="12" r="9" fill="currentColor"/></svg>
            @veloran.cabinets
          </li>
        </ul>
      </div>
    </section>
  </main>
</body>
</html>
```